Exclusive beauty salon needs a price list or services booklet

I need a new very attractive flyer for my beauty salon, containing information on the different services and their prices.
In attachment you can find a pdf of the "old" one, but I'd love to have a beautifully designed new one!
I'd love to have a booklet in format 148 x 148 mm, or in US format, containing 12 or 16 pages, but if you can offer other nice looking designs they are welcome!
The services that need to come in the booklet with their prices can all be found on my website: www.atelierverano.be, starting with
Gelaatsverzorging
Wimperverlenging
Suikerontharing
Wimperlifting
Permanente Make Up
Airbrush Tanning

Target Market(s)

woman from 20 to 89 years old

Industry/Entity Type

Beauty Salon

Font styles to use
Sans Serif

Colors

Designer to choose colors to be used in the design.

Requirements
Must have
• a classy nice look, it must contain details about the services from my beauty salon and their prices, and nice pictures.
• The Names, prices and explanations of the services can easily be found on my website: www.atelierverano.be
Nice to have
• In attachment you can find the "old" price list in pdf, what I need now is a "new booklet" with the new logo and updated services price list.
• I need a very nice and attractive looking booklet, classy chique, Paris chique, looking very expensive.
Should not have
• Not too much colors, not too curly, but still feminine

```html
<!DOCTYPE html>
<html lang="nl">
<head>
<meta charset="utf-8">
<title>Atelier Verano – Testimonials</title>
<link rel="stylesheet" href="https://fonts.googleapis.com/css2?family=Didact+Gothic&family=Montserrat:wght@600&display=swap">
<style>
  :root {
    --backdrop: #a9a9a9;
    --paper: #ffffff;
    --paper-shade: #ececec;
    --rose: #dba5ab;
    --rose-light: #f3d9dc;
    --ink: #6a6a6a;
    --accent-text: #d99aa1;
    --folio: #b5b5b5;
  }
  * { margin: 0; padding: 0; box-sizing: border-box; }
  html, body {
    width: 1200px;
    height: 523px;
    overflow: hidden;
    background: var(--backdrop);
  }
  .spread {
    position: absolute;
    left: 264px;
    top: 80px;
    width: 674px;
    height: 355px;
    display: flex;
    gap: 3px;
  }
  .page {
    position: relative;
    width: 50%;
    height: 100%;
    background: var(--paper);
  }
  .page--left {
    background: linear-gradient(to right, var(--paper) 70%, var(--paper-shade) 100%);
  }
  .page--right {
    background: linear-gradient(to left, var(--paper) 75%, var(--paper-shade) 100%);
  }
  .title-band {
    position: absolute;
    left: 0;
    right: 0;
    top: 44px;
    height: 31px;
    background: linear-gradient(to right, var(--rose) 70%, var(--rose-light) 92%, var(--rose) 100%);
    display: flex;
    align-items: center;
    justify-content: center;
  }
  .title-band h2 {
    font-family: "Montserrat", sans-serif;
    font-weight: 600;
    font-size: 12px;
    letter-spacing: 0.3px;
    color: var(--paper);
    padding-left: 8px;
  }
  .testimonial {
    position: absolute;
    left: 24px;
    right: 18px;
    text-align: center;
    font-family: "Didact Gothic", sans-serif;
    text-transform: uppercase;
  }
  .testimonial--first { top: 138px; }
  .testimonial--second { top: 249px; }
  .testimonial blockquote {
    font-size: 8px;
    line-height: 16px;
    color: var(--ink);
  }
  .testimonial cite {
    display: block;
    margin-top: 15px;
    font-style: normal;
    font-size: 8px;
    color: var(--accent-text);
  }
  .folio {
    position: absolute;
    right: 6px;
    bottom: 16px;
    font-family: "Didact Gothic", sans-serif;
    font-size: 8px;
    color: var(--folio);
  }
</style>
</head>
<body>
  <main class="spread">
    <section class="page page--left">
      <div class="title-band"><h2>TESTIMONIALS</h2></div>

      <figure class="testimonial testimonial--first">
        <blockquote>"Ik ben al jaren klant bij Mireille en wordt nog steeds met hetzelfde<br>enthousiasme ontvangen. Ik kom altijd helemaal zen buiten!"</blockquote>
        <cite>Noor / Zelfstandige / Deinze</cite>
      </figure>

      <figure class="testimonial testimonial--second">
        <blockquote>"Super blij met mijn wimpertjes!"</blockquote>
        <cite>Lotte &nbsp;/ Directieassistente / Zomergem</cite>
      </figure>
    </section>

    <section class="page page--right">
      <span class="folio">1</span>
    </section>
  </main>
</body>
</html>
```